Brindle Yard Care. The best in the biz

I run a lawn care service that offers full service mowing. 100% satisfaction guarantee. Fast, Friendly, quality service "I am your lawns best friend" I cut residential lawns. I offer a mow package that includes trimming, edging and clean up. Prices very from 20 dollars to 75. I want my logo to stand out. Free estimates

Target Market(s)

Home owners

Industry/Entity Type

Landscaping

Contact Information for Business Card

555-812-4473 tomvale48@quillmail.net Derek. Brindle Yard care

Colors
f37122
9bcb3c
cadf82

Requirements
Must have
• Company name.
• Phone number
• Email
• My services
• images
Nice to have
• A sun that is growing grass.
Should not have
• Incorrect information

```html
<!DOCTYPE html>
<html lang="en">
<head>
<meta charset="utf-8">
<title>Brindle Yard Care – Business Card</title>
<link rel="stylesheet" href="https://fonts.googleapis.com/css2?family=Source+Sans+3:ital,wght@0,400;0,600;1,600&display=swap">
<style>
  :root {
    --orange: #f28c22;
    --orange-deep: #e9821a;
    --green: #1f9a3e;
    --white: #ffffff;
    --backdrop: #e9e6e2;
    --watermark: #f1f1f1;
  }
  html, body {
    margin: 0;
    width: 1200px;
    height: 900px;
    overflow: hidden;
    background: var(--backdrop);
    font-family: "Source Sans 3", Arial, sans-serif;
  }
  .stage { position: relative; width: 1200px; height: 900px; }
  .card {
    position: absolute;
    background: var(--white);
    overflow: hidden;
    box-shadow: 0 6px 18px rgba(0,0,0,0.12);
  }
  .card-front { left: 78px; top: 35px; width: 588px; height: 363px; }
  .card-back  { left: 388px; top: 505px; width: 567px; height: 352px; }

  .brand {
    position: absolute; left: 30px; top: 62px;
    display: flex; align-items: center; gap: 14px;
  }
  .brand-dot { width: 34px; height: 34px; border-radius: 50%; background: var(--orange); }
  .brand-name {
    margin: 0; font-size: 46px; font-weight: 600; color: var(--green);
    letter-spacing: 0.5px; line-height: 1;
  }

  .contact-band {
    position: absolute; left: 0; right: 0; top: 197px; bottom: 0;
    background: var(--orange); color: var(--white);
  }
  .band-ring { position: absolute; left: 280px; top: -20px; }
  .contact-name {
    position: absolute; left: 30px; top: 30px; margin: 0;
    font-size: 22px; font-weight: 600;
  }
  .contact-list {
    position: absolute; left: 30px; top: 82px; margin: 0; padding: 0;
    list-style: none; font-size: 15.5px; line-height: 25px;
  }
  .contact-list li { display: flex; align-items: center; gap: 6px; }
  .contact-list svg { width: 11px; height: 11px; fill: var(--white); }

  .back-ring { position: absolute; left: 77px; top: -5px; }
  .promise-band {
    position: absolute; left: 0; right: 0; top: 110px; height: 130px;
    background: var(--orange); color: var(--white); text-align: center;
  }
  .promise-title { margin: 18px 0 0; font-size: 20px; font-weight: 600; }
  .promise-values { margin: 6px 0 0; font-size: 17px; font-weight: 600; word-spacing: 2px; }
  .promise-tagline { margin: 13px 0 0; font-size: 23px; font-weight: 600; font-style: italic; }
</style>
</head>
<body>
<main class="stage">
  <section class="card card-front" aria-label="Business card front">
    <div class="brand">
      <span class="brand-dot"></span>
      <h1 class="brand-name">Brindle Yard Care</h1>
    </div>
    <div class="contact-band">
      <svg class="band-ring" width="340" height="340" viewBox="0 0 340 340" aria-hidden="true">
        <circle cx="170" cy="170" r="150" fill="none" stroke="var(--orange-deep)" stroke-width="24"/>
      </svg>
      <h2 class="contact-name">Derek</h2>
      <ul class="contact-list">
        <li>
          <svg viewBox="0 0 24 24" aria-hidden="true"><path d="M6.6 10.8a15.1 15.1 0 0 0 6.6 6.6l2.2-2.2c.3-.3.7-.4 1-.2 1.1.4 2.3.6 3.6.6.6 0 1 .4 1 1V20c0 .6-.4 1-1 1A17 17 0 0 1 3 4c0-.6.4-1 1-1h3.5c.6 0 1 .4 1 1 0 1.3.2 2.5.6 3.6.1.3 0 .7-.2 1z"/></svg>
          555-812-4473
        </li>
        <li>
          <svg viewBox="0 0 24 24" aria-hidden="true"><path d="M2 5h20v14H2z M3 6l9 7 9-7" stroke="var(--orange)" stroke-width="1.5"/></svg>
          tomvale48@quillmail.net
        </li>
      </ul>
    </div>
  </section>

  <section class="card card-back" aria-label="Business card back">
    <svg class="back-ring" width="380" height="380" viewBox="0 0 380 380" aria-hidden="true">
      <circle cx="190" cy="190" r="165" fill="none" stroke="var(--watermark)" stroke-width="26"/>
    </svg>
    <div class="promise-band">
      <p class="promise-title">100% satisfaction guarantee.</p>
      <p class="promise-values">Fast | Friendly | Quality Service</p>
      <p class="promise-tagline">I am your lawns best friend</p>
    </div>
  </section>
</main>
</body>
</html>
```